New Zealand Marlborough Sauvignon Blanc wine packaging design

We need packaging design for our new wine brand, Dunmore Vale. The wine is a New Zealand Marlborough Sauvignon Blanc. We would like the packaging will portray elegance and style with an understated label. We are looking for a label that portrays the elegance of the French Riviera. The label should be round or pill shaped.
Updates

Industry/Entity Type

Wine

Font styles to use
Serif
Sans Serif

Requirements
Must have
• The words in order of importance: Dunmore Vale, Sauvignon Blanc, Marlborough, New Zealand. It should be fit to the bottle posted in the links
Nice to have
• a pill shape or circular shape
Should not have
• Illustrations of wine bottles, wine glasses, or grapes

```html
<!DOCTYPE html>
<html lang="en">
<head>
<meta charset="utf-8">
<title>Dunmore Vale — Sauvignon Blanc Label</title>
<link rel="stylesheet" href="https://fonts.googleapis.com/css2?family=Playfair+Display:wght@600;700;800&display=swap">
<style>
  :root {
    --label-teal: #268c7a;
    --label-white: #ffffff;
    --canvas-bg: #ffffff;
  }
  html, body {
    margin: 0;
    padding: 0;
    width: 1200px;
    height: 675px;
    overflow: hidden;
    background: var(--canvas-bg);
  }
  .label-canvas {
    display: block;
    width: 1200px;
    height: 675px;
  }
  .label-ring {
    fill: var(--label-white);
    stroke: var(--label-teal);
    stroke-width: 7;
  }
  .label-band { fill: var(--label-teal); }
  .crest-area { fill: var(--label-teal); }
  .brand-name {
    font-family: "Playfair Display", serif;
    font-weight: 800;
    font-size: 98px;
    fill: var(--label-teal);
    letter-spacing: -2px;
  }
  .varietal {
    font-family: "Playfair Display", serif;
    font-weight: 700;
    font-size: 34px;
    fill: var(--label-white);
  }
  .region {
    font-family: "Playfair Display", serif;
    font-weight: 700;
    font-size: 17px;
    fill: var(--label-white);
    letter-spacing: 0.5px;
  }
</style>
</head>
<body>
<svg class="label-canvas" viewBox="0 0 1200 675" xmlns="http://www.w3.org/2000/svg">
  <defs>
    <clipPath id="label-shape">
      <circle cx="600" cy="337" r="296"/>
    </clipPath>
    <path id="region-arc" d="M 350 337 A 250 250 0 0 0 850 337"/>
  </defs>

  <g class="wine-label">
    <circle class="label-ring" cx="600" cy="337" r="296"/>
    <rect class="label-band" x="300" y="393" width="600" height="260" clip-path="url(#label-shape)"/>

    <rect class="crest-area" x="584" y="52" width="32" height="148" rx="16"
          role="img" aria-label="Slender flowing ornamental crest hanging from the top of the label"/>

    <text class="brand-name" x="600" y="290" text-anchor="middle">Dunmore</text>
    <text class="brand-name" x="600" y="385" text-anchor="middle">Vale</text>

    <text class="varietal" x="600" y="492" text-anchor="middle">Sauvignon Blanc</text>

    <text class="region">
      <textPath href="#region-arc" startOffset="50%" text-anchor="middle">Marlborough  ·  New Zealand</textPath>
    </text>
  </g>
</svg>
</body>
</html>
```